Homemaking training schools needs a Business Card design

Designer, Hello!

No special requirements, good-looking enough.
--------------------------------------------------------------------------

Name: Marcus Dole
Chairman
Tel: 0574-71948263
Mobile: 13857420916
Email: kelvora@mailnest.example
Web: www.prt2019.example
Add: No.258, LanpingJie, BeiyuanQu, Ningbo, Zhejiang

LOGO
Ningbo PRT Homemaking Training School

Target Market(s)

pregnant women, mothers, infants, the elderly and families, including cleaning, cooking, nursing training.

Industry/Entity Type

Business

Contact Information for Business Card

Name: Marcus Dole
Chairman
Tel: 0574-71948263
Mobile: 13857420916
Email: kelvora@mailnest.example
Web: www.prt2019.example

LOGO

Font styles to use
Serif
Sans Serif
Decorative

Requirements
Nice to have
• Feels: clean, specifications, safety, comfort, warmth and happiness.

```html
<!DOCTYPE html>
<html lang="en">
<head>
<meta charset="utf-8">
<title>PingRuiTang Business Card</title>
<link rel="stylesheet" href="https://fonts.googleapis.com/css2?family=Arimo:wght@400;700&display=swap">
<style>
  :root {
    --blue: #1c72b8;
    --blue-deep: #155a94;
    --blue-light: #2f86cc;
    --pink: #e0198a;
    --ink: #4a4a4a;
    --paper: #ffffff;
    --backdrop: #e9e6e1;
    --back-soft: #dbe7f3;
  }
  * { box-sizing: border-box; margin: 0; padding: 0; }
  html, body {
    width: 1200px; height: 950px; overflow: hidden;
    background: var(--backdrop);
    font-family: "Arimo", Arial, sans-serif;
  }
  .sheet {
    width: 1200px; height: 950px;
    display: flex; flex-direction: column; align-items: center; justify-content: center;
    gap: 40px;
  }
  .card {
    position: relative;
    width: 700px; height: 420px;
    border-radius: 4px;
    overflow: hidden;
    box-shadow: 0 6px 18px rgba(0,0,0,0.18);
  }

  /* Front */
  .card-front { background: var(--paper); }
  .name-band {
    position: absolute; left: 0; top: 92px;
    width: 380px; height: 68px;
    background: var(--blue);
    padding: 12px 0 0 40px;
    color: #fff;
  }
  .name-band .person { font-size: 24px; font-weight: 700; letter-spacing: 0.3px; }
  .name-band .role { font-size: 14px; margin-top: 2px; }

  .company {
    position: absolute; left: 400px; top: 104px;
    width: 270px; height: 44px;
    display: flex; align-items: center; justify-content: center;
    font-size: 30px; font-weight: 400; color: var(--blue);
  }
  .pink-tab {
    position: absolute; right: 0; top: 118px;
    width: 18px; height: 54px; background: var(--pink);
  }

  .contacts {
    position: absolute; left: 40px; top: 262px;
    list-style: none;
    font-size: 16px; color: var(--ink);
  }
  .contacts li { display: flex; align-items: center; gap: 8px; line-height: 26px; }
  .contacts svg { width: 16px; height: 16px; fill: var(--blue); flex: none; }

  .address {
    position: absolute; right: 40px; top: 296px;
    text-align: right; font-size: 16px; color: var(--ink); line-height: 24px;
  }
  .address .web { color: var(--blue); font-weight: 700; margin-top: 4px; }

  /* Back */
  .card-back {
    background: linear-gradient(135deg, var(--blue-light) 0%, var(--blue) 50%, var(--blue-deep) 100%);
    display: flex; flex-direction: column; align-items: center; justify-content: center;
  }
  .card-back .company-name { font-size: 40px; font-weight: 400; color: #fff; }
  .card-back .web { margin-top: 26px; font-size: 16px; letter-spacing: 2px; color: var(--back-soft); }
</style>
</head>
<body>
<main class="sheet">
  <section class="card card-front">
    <div class="name-band">
      <div class="person">Marcus Dole</div>
      <div class="role">Chairman</div>
    </div>

    <div class="company">PingRuiTang</div>
    <div class="pink-tab"></div>

    <ul class="contacts">
      <li>
        <svg viewBox="0 0 16 16" aria-hidden="true"><path d="M2 5c0-2 3-3 6-3s6 1 6 3v1h-3V5H5v1H2zM4 7h8l2 6H2z"/></svg>
        0574-71948263
      </li>
      <li>
        <svg viewBox="0 0 16 16" aria-hidden="true"><path d="M4 1h8v14H4zM5.5 3v9h5V3zM7 13h2v1H7z" fill-rule="evenodd"/></svg>
        13857420916
      </li>
      <li>
        <svg viewBox="0 0 16 16" aria-hidden="true"><path d="M1 3h14v10H1zM2 4l6 5 6-5z" fill-rule="evenodd"/></svg>
        kelvora@mailnest.example
      </li>
    </ul>

    <div class="address">
      <div>No.258, LanpingJie</div>
      <div>BeiyuanQu, Ningbo, Zhejiang</div>
      <div class="web">www.prt2019.example</div>
    </div>
  </section>

  <section class="card card-back">
    <div class="company-name">PingRuiTang</div>
    <div class="web">www.prt2019.example</div>
  </section>
</main>
</body>
</html>
```